Brindle Sky Port needs a new upscale business card design for our high end aircraft hangar complex

Brindle Sky Port (BSP) is a large, upscale jet hangar complex in the US housing expensive aircraft. We need a new business card design, using our current logo. We will be attending a industry convention and need a card design that will stand out and be remembered by aircraft owners and private pilots.

Target Market(s)

Aircraft pilots or owners looking for a new upscale hangar

Industry/Entity Type

Airport

Contact Information for Business Card

I like to use very heavy card stock, 400#, double sided. Square, no rounded edges please.

Colors
3276b5
0255a3
85abd2

Requirements
Must have
• An expensive, classy design, vivid colors.
Nice to have
• Needs to look very expensive and classy, and have some "pop". Designer must be able to download or copy my current typeface or fonts.
• One card side might be black with the "Logo and Brindle Sky Port Double line image in blue (or try gold, or glossy black), and perhaps have a grayed out "K720 jet silhouette". The other card side would have our contact info, and perhaps the "BSP Logo only". I'd like my contact info 'stacked', not in a paragraph format.
Should not have
• Should not look "too busy". Having a double-sided card will help.

```html
<!DOCTYPE html>
<html lang="en">
<head>
<meta charset="utf-8">
<title>Brindle Sky Port – Business Card</title>
<link rel="stylesheet" href="https://fonts.googleapis.com/css2?family=Arimo:wght@400;700&display=swap">
<style>
  :root {
    --backdrop: #4a423d;
    --card: #1c1d1f;
    --silver: #d9dadc;
    --blue: #3276b5;
    --blue-deep: #0255a3;
    --blue-light: #85abd2;
    --white: #f2f2f2;
    --rule: #8a8c90;
  }
  * { box-sizing: border-box; margin: 0; padding: 0; }
  html, body { width: 1200px; height: 787px; overflow: hidden; }
  body {
    background: var(--backdrop);
    font-family: "Arimo", Arial, sans-serif;
    position: relative;
  }
  .card {
    position: absolute;
    width: 540px;
    height: 309px;
    background: var(--card);
    box-shadow: 0 10px 30px rgba(0,0,0,.45);
  }
  .card-front { left: 40px; top: 110px; }
  .card-back { left: 620px; top: 368px; }

  .front-brand {
    position: absolute;
    left: 0; right: 0; top: 96px;
    text-align: center;
    color: var(--silver);
  }
  .front-name {
    font-weight: 700;
    font-size: 40px;
    letter-spacing: 1px;
    text-transform: uppercase;
  }
  .front-web {
    margin-top: 44px;
    font-size: 15px;
    letter-spacing: 3px;
  }

  .back-brand {
    position: absolute;
    left: 40px; top: 112px;
    width: 220px;
    text-align: center;
    color: var(--blue);
    font-weight: 700;
    font-size: 68px;
    letter-spacing: 2px;
  }
  .divider {
    position: absolute;
    left: 285px; top: 40px;
    width: 1px; height: 230px;
    background: linear-gradient(var(--card), var(--rule), var(--card));
  }
  .contact {
    position: absolute;
    left: 305px; top: 48px;
    color: var(--white);
    font-size: 15px;
    line-height: 1.3;
  }
  .contact-name { color: var(--blue); font-size: 20px; }
  .contact-title { font-size: 17px; margin-bottom: 10px; }
  .contact-address { margin-bottom: 6px; }
  .contact-list { list-style: none; }
  .contact-list li { display: flex; align-items: center; gap: 8px; height: 21px; }
  .contact-list svg { width: 13px; height: 13px; fill: var(--blue-light); flex: none; }
  .contact-web { margin-top: 2px; }
</style>
</head>
<body>
  <section class="card card-front" aria-label="Card front">
    <div class="front-brand">
      <div class="front-name">Brindle Sky Port</div>
      <div class="front-web">www.brindlesky.com</div>
    </div>
  </section>

  <section class="card card-back" aria-label="Card back">
    <div class="back-brand">BSP</div>
    <div class="divider"></div>
    <div class="contact">
      <div class="contact-name">Alan Reyes</div>
      <div class="contact-title">President</div>
      <div class="contact-address">4120 Harrow Field Road<br>Dunmore, NY 12790</div>
      <ul class="contact-list">
        <li><svg viewBox="0 0 16 16" aria-hidden="true"><path d="M3 1l3 3-1.5 2a9 9 0 0 0 5.5 5.5L12 10l3 3-2 2C7 15 1 9 1 3z"/></svg>555 0142 7781</li>
        <li><svg viewBox="0 0 16 16" aria-hidden="true"><path d="M4 0h8v16H4zM5.5 2v10h5V2z"/></svg>555 0193 4420</li>
        <li><svg viewBox="0 0 16 16" aria-hidden="true"><path d="M4 1h7v4H4zM1 6h14v7h-3v2H4v-2H1zM5 10v4h6v-4z"/></svg>555 0167 2098</li>
        <li><svg viewBox="0 0 16 16" aria-hidden="true"><path d="M1 3h14v10H1zM2.5 4.5L8 9l5.5-4.5z"/></svg>alan@brindlesky.com</li>
        <li class="contact-web"><svg viewBox="0 0 16 16" aria-hidden="true"><circle cx="8" cy="8" r="7"/></svg>www.brindlesky.com</li>
      </ul>
    </div>
  </section>
</body>
</html>
```